Vantro cards

I am in the auto motive, transportation business I would like a business card that is Something cool, modern edgy, having to do with car culture. I offer towing service for high and exotic cars. I also provide towing for collisions and car accidents. I offer open and enclosed transport nationwide.

Target Market(s)

Car culture people high end auto collectors

Industry/Entity Type

Towing car carrier

Contact Information for Business Card

My company colors black yellow and silver

Font styles to use
Serif

```html
<!DOCTYPE html>
<html lang="en">
<head>
<meta charset="utf-8">
<title>Vantro Transportation – Business Card</title>
<link rel="stylesheet" href="https://fonts.googleapis.com/css2?family=Montserrat:wght@400;500;700&display=swap">
<style>
  :root {
    --black: #0b0b0b;
    --yellow: #f9dd4a;
    --white: #ffffff;
    --silver-light: #f4f4f4;
    --silver-mid: #c9c9c9;
    --silver-dark: #8e8e8e;
    --backdrop: #d9d4cc;
  }
  * { margin: 0; padding: 0; box-sizing: border-box; }
  html, body {
    width: 900px; height: 1200px; overflow: hidden;
    background: var(--backdrop);
    font-family: "Montserrat", Arial, sans-serif;
  }
  .card {
    position: absolute; left: 80px; width: 742px; height: 443px;
    border-radius: 28px; overflow: hidden;
  }
  .card-front { top: 132px; background: var(--white); }
  .card-back {
    top: 638px; height: 440px;
    background:
      conic-gradient(from 20deg at 50% 45%,
        var(--silver-light), var(--silver-dark) 12%, var(--silver-light) 25%,
        var(--silver-mid) 38%, var(--silver-light) 50%, var(--silver-dark) 62%,
        var(--silver-light) 75%, var(--silver-mid) 88%, var(--silver-light));
  }
  .brand-name {
    position: absolute; text-align: center;
    font-weight: 700; color: var(--black); line-height: 1.1;
    text-transform: uppercase;
  }
  .card-front .brand-name { left: 38px; top: 95px; width: 190px; font-size: 30px; }
  .card-front .brand-name small { display: block; font-size: 15px; letter-spacing: 0.5px; }
  .card-back .brand-name { left: 0; right: 0; top: 180px; font-size: 56px; }
  .card-back .brand-name small { display: block; font-size: 24px; letter-spacing: 1px; }
  .name-tab {
    position: absolute; left: 0; top: 268px; width: 262px; height: 58px;
    background: var(--yellow);
    clip-path: polygon(0 0, 238px 0, 100% 100%, 0 100%);
    padding: 4px 0 0 28px;
  }
  .person-name { font-size: 25px; font-weight: 700; color: var(--black); }
  .person-role { font-size: 15px; font-weight: 400; color: var(--black); margin-top: -2px; }
  .accent-stripe {
    position: absolute; left: 260px; right: 0; top: 304px; height: 12px;
    background: var(--black);
    clip-path: polygon(0 0, 100% 0, 100% 100%, 6px 100%);
  }
  .contact-band {
    position: absolute; left: 0; right: 0; top: 328px; bottom: 0;
    background: var(--black); color: var(--white);
  }
  .contact-list { position: absolute; left: 28px; top: 22px; list-style: none; font-size: 16.5px; }
  .contact-list li { display: flex; align-items: center; height: 21.5px; }
  .contact-list svg { width: 13px; height: 13px; margin-right: 12px; fill: var(--yellow); }
  .address {
    position: absolute; left: 502px; top: 44px; font-size: 16.5px; line-height: 21.5px;
    padding-left: 20px; border-left: 2px solid var(--yellow);
  }
</style>
</head>
<body>
  <section class="card card-front">
    <div class="brand-name">Vantro<small>Transportation</small></div>
    <div class="name-tab">
      <div class="person-name">Dario Kessler</div>
      <div class="person-role">Owner</div>
    </div>
    <div class="accent-stripe"></div>
    <div class="contact-band">
      <ul class="contact-list">
        <li><svg viewBox="0 0 16 16"><path d="M3 1h3l1.5 4-2 1.2a9 9 0 0 0 4.3 4.3L11 8.5l4 1.5v3a2 2 0 0 1-2 2A13 13 0 0 1 1 3a2 2 0 0 1 2-2z"/></svg>(555) 214-0937</li>
        <li><svg viewBox="0 0 16 16"><path d="M1 3h14v1.5L8 9 1 4.5z M1 6.3l7 4.4 7-4.4V13H1z"/></svg>info@vantrotransportation.com</li>
        <li><svg viewBox="0 0 16 16"><circle cx="8" cy="8" r="7"/></svg>www.vantrotransportation.com</li>
      </ul>
      <div class="address">48 Ridgeway Lane<br>Millbrook, PA 17500</div>
    </div>
  </section>

  <section class="card card-back">
    <div class="brand-name">Vantro<small>Transportation</small></div>
  </section>
</body>
</html>
```